redesign of my existing custom website into Wordpress based website

I need someone to redesign my current website into something more classy, simplistic, modern and on trend. I would like it set up on Wordpress in a way thats easy for me to make my own additions to blogs/price changes and promotion banners. I will also need a page that is password protected so members can login and have access to all my training videos and resources.
website is www.tidewellmamas.com.au

Target Market(s)

new mums

Industry/Entity Type

Fitness

Coding

Coded - Design and coding required

Number of Pages Required

5+ page

Colors
33a6d7

Requirements
Must have
• chic, modern, stylish and simplistic.
• a call to action above the page fold
• mobile friendly conversion
• a pop up message as soon as someone enters my sight offering my free report
• a members page that is password protected containing 3 youtube videos and 6 pdf attachments as resources
• a home page
• a contact us page
• an about us page
• a blog page
• a store page
Nice to have
• some examples of my peers websites that I like:
• www.norapellwick.com
• https://www.9qlr.com
• https://41bytedgarth.com
Should not have
• anything gimmicky

```html
<!DOCTYPE html>
<html lang="en">
<head>
<meta charset="utf-8">
<title>Tidewell Mamas – Home Fitness</title>
<link href="https://fonts.googleapis.com/css2?family=Open+Sans:wght@400;600;700&display=swap" rel="stylesheet">
<style>
:root{
  --blue:#33a6d7;
  --navy:#1d3a52;
  --navy-deep:#142b3e;
  --pink:#d8197d;
  --ink:#2b2b2b;
  --grey:#6c6c6c;
  --light:#f2f4f6;
  --line:#e1e4e8;
  --white:#ffffff;
  --shade:rgba(0,0,0,.74);
}
*{box-sizing:border-box;margin:0;padding:0}
html,body{width:1200px;height:5070px;overflow:hidden}
body{font-family:"Open Sans",Arial,sans-serif;color:var(--ink);background:var(--white);position:relative}
.abs{position:absolute}
section,header,footer{position:absolute;left:0;width:1200px}

/* header */
.site-header{top:0;height:40px;background:var(--white)}
.nav-bar{position:absolute;left:405px;right:0;top:0;height:40px;background:var(--navy);display:flex;align-items:center;gap:34px;padding-left:40px;font-size:12px;color:var(--white);text-transform:uppercase;letter-spacing:.5px}
.nav-bar .members{margin-left:auto;background:var(--blue);height:40px;display:flex;align-items:center;padding:0 26px}
.brand-badge{position:absolute;left:130px;top:0;width:180px;height:150px;border-radius:0 0 90px 90px;background:var(--white);display:flex;flex-direction:column;align-items:center;justify-content:center;z-index:2;box-shadow:0 2px 6px rgba(0,0,0,.2)}
.brand-badge .name{font-size:16px;font-weight:600;color:var(--pink)}
.brand-badge .sub{font-size:10px;color:var(--grey);letter-spacing:1px;margin-top:2px}

/* hero */
.hero{top:40px;height:570px;background:linear-gradient(100deg,#e9ecef 0%,#d7dadd 45%,#b9b2aa 70%,#8f8a86 100%)}
.hero-copy{left:130px;top:160px;width:420px}
.hero-copy h1{font-size:27px;font-weight:700;color:var(--ink)}
.hero-copy p{font-size:13px;color:var(--grey);margin-top:6px}
.hero-field{margin-top:18px;width:340px;height:40px;border:1px solid #bbb;background:var(--white);font-size:12px;color:#999;padding:11px 14px}

/* intro */
.intro{top:610px;height:340px;background:var(--white)}
.intro h2{position:absolute;left:130px;top:80px;font-size:25px;color:var(--blue);font-weight:700}
.intro .lead{position:absolute;left:130px;top:120px;font-size:14px;font-weight:600}
.intro-list{position:absolute;left:130px;top:160px;width:640px;display:grid;grid-template-columns:1fr 1fr;row-gap:16px;column-gap:20px;font-size:12px;color:var(--grey)}
.intro-list li{list-style:none;display:flex;gap:8px;align-items:center}
.offer-box{position:absolute;left:818px;top:83px;width:248px;height:192px;background:var(--blue);color:var(--white);text-align:center;padding:20px 18px}
.offer-box p{font-size:13px;line-height:1.4}
.offer-box strong{display:block;font-size:15px;margin-top:10px}
.offer-box .btn{margin-top:14px}

/* buttons */
.btn{display:inline-block;background:var(--blue);color:var(--white);font-size:12px;font-weight:700;text-transform:uppercase;padding:12px 22px;letter-spacing:.5px}
.btn.on-blue{background:var(--navy)}

/* packs */
.pack{background:var(--white)}
.pack-equip{top:950px;height:1000px;background:var(--light)}
.pack-basic{top:1950px;height:960px;background:var(--white)}
.pack h2{position:absolute;left:0;width:1200px;text-align:center;font-size:30px;font-weight:700}
.pack h3{position:absolute;left:0;width:1200px;text-align:center;font-size:24px;color:var(--blue);font-weight:400}
.pack .note{position:absolute;left:0;width:1200px;text-align:center;font-size:13px;color:var(--grey)}
.features{position:absolute;left:130px;width:940px;display:grid;grid-template-columns:1fr 1fr;column-gap:60px}
.feature{height:140px}
.feature h4{font-size:15px;color:var(--blue);font-weight:600;display:flex;gap:10px;align-items:center}
.feature p{font-size:12px;color:var(--grey);line-height:1.6;margin-top:8px;padding-left:28px}
.feature.solo{position:absolute;left:380px;width:440px}
.price{position:absolute;left:0;width:1200px;text-align:center;font-size:15px}
.price b{font-size:40px;color:var(--blue);font-weight:400;vertical-align:middle;margin:0 6px}
.price small{font-size:11px;color:var(--grey)}
.center-btn{position:absolute;left:0;width:1200px;text-align:center}
.postage{position:absolute;left:0;width:1200px;text-align:center;font-size:11px;color:var(--grey);text-transform:uppercase}
.product-shot{position:absolute;background:linear-gradient(135deg,#d23d8c,#f0a0c4 45%,#2a2a2a);box-shadow:0 3px 10px rgba(0,0,0,.25)}

/* why */
.why{top:2910px;height:920px;background:var(--white)}
.why h2{position:absolute;left:130px;top:40px;font-size:28px;font-weight:600}
.card{position:absolute;width:300px}
.card .photo{height:180px;background:linear-gradient(135deg,#c8b8a8,#8d7a6a)}
.card h5{font-size:12px;font-weight:700;text-transform:uppercase;margin-top:14px}
.card p{font-size:11px;color:var(--grey);line-height:1.6;margin-top:8px}
.card .more{font-size:11px;color:var(--blue);margin-top:8px;display:block}
.side{position:absolute;left:802px;width:264px}
.social-box{top:108px;height:175px;background:var(--white);border:1px solid var(--line)}
.social-box .top{height:60px;background:linear-gradient(135deg,#7d9fb5,#3c5d75)}
.social-box .title{font-size:13px;font-weight:700;padding:10px 12px}
.social-box .faces{display:flex;gap:6px;padding:0 12px}
.social-box .faces span{width:30px;height:30px;background:#cfd6dc}
.side-cta{top:300px;height:255px;background:var(--blue);color:var(--white);padding:26px 22px;text-align:center}
.side-cta p{font-size:13px;line-height:1.5;text-transform:uppercase;font-weight:600}
.side-cta .btn{margin-top:22px;background:var(--white);color:var(--blue)}
.side-join{top:570px;height:240px;background:var(--navy);color:var(--white);padding:22px 18px;font-size:12px;line-height:1.5;text-transform:uppercase;font-weight:600}
.side-join .photo{position:absolute;right:0;top:0;width:110px;height:240px;background:linear-gradient(180deg,#b89a86,#6c5646)}
.side-join p{width:130px}
.side-join .btn{position:absolute;left:18px;bottom:22px;font-size:10px;padding:9px 14px}

/* news */
.news{top:3830px;height:270px;background:var(--white)}
.news h2{position:absolute;left:130px;top:30px;font-size:28px;font-weight:600}
.news-arrows{position:absolute;right:135px;top:40px;display:flex;gap:4px}
.news-arrows span{width:22px;height:22px;background:var(--light)}
.news-item{position:absolute;top:92px;width:290px;display:flex;gap:14px}
.news-item .thumb{flex:none;width:66px;height:66px;background:linear-gradient(135deg,#d3b48a,#8c6a42)}
.news-item h6{font-size:12px;font-weight:600;line-height:1.4}
.news-item time{font-size:10px;color:var(--grey)}

/* compare */
.compare{top:4100px;height:800px;background:var(--white)}
.compare h2{position:absolute;left:0;width:1200px;text-align:center;top:30px;font-size:30px;font-weight:700;line-height:1.3}
.compare h3{position:absolute;left:0;width:1200px;text-align:center;top:110px;font-size:22px;color:var(--blue);font-weight:400}
.compare-table{position:absolute;left:130px;top:175px;width:940px;border-collapse:collapse;font-size:12px;table-layout:fixed}
.compare-table th{background:var(--blue);color:var(--white);height:78px;font-size:12px;font-weight:600;padding:0 12px;text-align:center}
.compare-table th:first-child{width:340px}
.compare-table td{height:80px;border-bottom:1px solid var(--line);text-align:center}
.compare-table td:first-child{text-align:left;padding-left:34px}
.compare-table tr:nth-child(even) td{background:#f7f8f9}
.compare-table tfoot td{background:var(--navy) !important;color:var(--white);height:72px;font-weight:700}

/* footer */
.site-footer{top:4900px;height:170px;background:var(--navy-deep);color:#9fb0bf;font-size:11px}
.foot-brand{position:absolute;left:150px;top:44px;font-size:15px;font-weight:600;color:var(--white)}
.foot-text{position:absolute;left:310px;top:42px;width:330px;line-height:1.6}
.foot-links{position:absolute;left:770px;top:42px;width:240px;line-height:1.6}
.foot-social{position:absolute;left:1005px;top:84px;display:flex;gap:8px}
.foot-social span{width:28px;height:28px;border-radius:50%;background:#5e7386}

/* modal */
.overlay{position:absolute;left:0;top:0;width:1200px;height:5070px;background:var(--shade);z-index:10}
.modal{position:absolute;left:405px;top:75px;width:400px;height:483px;background:var(--white);z-index:11}
.modal .photo{position:absolute;left:-40px;top:40px;width:210px;height:443px;background:linear-gradient(180deg,#b8b0a6 0%,#a9b48a 55%,#8d9180 100%)}
.modal .close{position:absolute;right:-12px;top:-12px;width:24px;height:24px;border-radius:50%;background:var(--white);border:2px solid #333}
.modal-logo{position:absolute;left:182px;top:30px;width:206px;text-align:center}
.modal-logo .dot{display:inline-block;width:40px;height:40px;border-radius:50%;border:2px solid var(--pink)}
.modal-logo .name{font-size:15px;font-weight:600;color:var(--pink);display:block;margin-top:6px}
.modal-body{position:absolute;left:182px;top:160px;width:206px}
.modal-body h2{font-size:17px;line-height:1.3;font-weight:700;color:var(--ink)}
.modal-body p{font-size:11px;line-height:1.5;color:var(--grey);margin-top:10px}
.modal-body p b{color:var(--pink);font-size:14px}
.modal-field{width:206px;height:34px;border:1px solid #ccc;font-size:10px;color:#999;text-align:center;line-height:32px;margin-top:14px}
.modal-body .btn{margin-top:20px;font-size:12px;padding:12px 16px}
</style>
</head>
<body>

<header class="site-header">
  <div class="brand-badge"><span class="name">Tidewell Mamas</span><span class="sub">HOME FITNESS</span></div>
  <nav class="nav-bar"><span>Home</span><span>About us</span><span>Program</span><span>Store</span><span>Blog</span><span>Contact us</span><span class="members">Member login</span></nav>
</header>

<section class="hero" role="img" aria-label="Photo of a mother exercising at home with her baby">
  <div class="abs hero-copy">
    <h1>Get your FREE TOP 10</h1>
    <p>Baby belly blasting tips sent straight to your inbox today</p>
    <div class="hero-field">Name</div>
  </div>
</section>

<section class="intro">
  <h2>Lose your baby weight and Bounce Back into shape!</h2>
  <div class="lead">12 Week Home Workout Program for Mums!</div>
  <ul class="intro-list">
    <li><svg width="14" height="14"><circle cx="7" cy="7" r="6" fill="#33a6d7"/></svg>12 weeks worth of workouts and training program</li>
    <li><svg width="14" height="14"><circle cx="7" cy="7" r="6" fill="#33a6d7"/></svg>Accountability charts &amp; progress sheets</li>
    <li><svg width="14" height="14"><circle cx="7" cy="7" r="6" fill="#33a6d7"/></svg>Train without DVD</li>
    <li><svg width="14" height="14"><circle cx="7" cy="7" r="6" fill="#33a6d7"/></svg>Family friendly healthy recipes</li>
    <li><svg width="14" height="14"><circle cx="7" cy="7" r="6" fill="#33a6d7"/></svg>Workout equipment delivered to your front door</li>
    <li><svg width="14" height="14"><circle cx="7" cy="7" r="6" fill="#33a6d7"/></svg>Healthy eating guidelines</li>
    <li><svg width="14" height="14"><circle cx="7" cy="7" r="6" fill="#33a6d7"/></svg>Weekly coaching emails</li>
  </ul>
  <div class="offer-box">
    <p>Start seeing amazing results in just a few weeks!</p>
    <strong>STARTING FROM ONLY $7.42 PER WEEK!</strong>
    <span class="btn on-blue">Get it here now!</span>
  </div>
</section>

<section class="pack pack-equip">
  <div class="product-shot" style="left:0;top:30px;width:150px;height:115px" role="img" aria-label="Program workbook and equipment pack"></div>
  <h2 style="top:100px">What's included in the program?</h2>
  <h3 style="top:145px">12 week Home Workout Program - Equipment Pack</h3>
  <p class="note" style="top:190px">Your purchase of the Home Workout Program - Equipment Pack comes loaded with value including:</p>
  <div class="features" style="top:235px">
    <div class="feature"><h4><svg width="18" height="18"><circle cx="9" cy="9" r="8" fill="#33a6d7"/><path d="M5 9l3 3 5-6" stroke="#fff" stroke-width="2" fill="none"/></svg>Full 3 stage 12 week training program</h4><p>Three progressive stages of home workouts built for busy mums, with clear videos and printable plans you can follow anywhere, any time of the day, at your own pace.</p></div>
    <div class="feature"><h4><svg width="18" height="18"><circle cx="9" cy="9" r="8" fill="#33a6d7"/><path d="M5 9l3 3 5-6" stroke="#fff" stroke-width="2" fill="none"/></svg>Full instructional manual DVD and program guide</h4><p>Every exercise explained step by step with photos and cues, so you always know how to move safely and get the most from each session.</p></div>
    <div class="feature"><h4><svg width="18" height="18"><circle cx="9" cy="9" r="8" fill="#33a6d7"/><path d="M5 9l3 3 5-6" stroke="#fff" stroke-width="2" fill="none"/></svg>Weekly accountability charts</h4><p>Track your sessions, measurements and wins each week to keep you motivated and on course through the whole twelve weeks.</p></div>
    <div class="feature"><h4><svg width="18" height="18"><circle cx="9" cy="9" r="8" fill="#33a6d7"/><path d="M5 9l3 3 5-6" stroke="#fff" stroke-width="2" fill="none"/></svg>Weekly coaching emails</h4><p>Friendly tips and reminders land in your inbox every week to guide your training, your meals and your mindset.</p></div>
    <div class="feature"><h4><svg width="18" height="18"><circle cx="9" cy="9" r="8" fill="#33a6d7"/><path d="M5 9l3 3 5-6" stroke="#fff" stroke-width="2" fill="none"/></svg>Fitness equipment delivered to your door</h4><p>Resistance bands, a mat and more, packed and posted so you can start training at home the day it arrives.</p></div>
    <div class="feature"><h4><svg width="18" height="18"><circle cx="9" cy="9" r="8" fill="#33a6d7"/><path d="M5 9l3 3 5-6" stroke="#fff" stroke-width="2" fill="none"/></svg>Nutritional advice and healthy eating</h4><p>Simple guidelines that fit family life, helping you fuel your body well without strict diets or complicated rules.</p></div>
  </div>
  <div class="feature solo" style="top:650px"><h4><svg width="18" height="18"><circle cx="9" cy="9" r="8" fill="#33a6d7"/><path d="M5 9l3 3 5-6" stroke="#fff" stroke-width="2" fill="none"/></svg>Healthy family friendly recipe book</h4><p>Quick, tasty meals the whole family will enjoy, made from everyday ingredients.</p></div>
  <div class="product-shot" style="left:940px;top:610px;width:230px;height:130px" role="img" aria-label="Printed program materials fanned out"></div>
  <p class="price" style="top:830px">One time only payment of <b>$199</b><small>*including GST</small> That's only $16.58 per week!</p>
  <div class="center-btn" style="top:895px"><span class="btn">Get started now</span></div>
  <p class="postage" style="top:943px">Free postage</p>
</section>

<section class="pack pack-basic">
  <h2 style="top:75px">Already have the equipment you need?</h2>
  <p class="note" style="top:118px">We have also made the program available with everything but the equipment.</p>
  <h3 style="top:150px">12 week Home Workout Program - Basic Pack</h3>
  <p class="note" style="top:192px">Your purchase of the Home Workout Program - Basic Pack includes:</p>
  <div class="features" style="top:230px">
    <div class="feature"><h4><svg width="18" height="18"><circle cx="9" cy="9" r="8" fill="#33a6d7"/><path d="M5 9l3 3 5-6" stroke="#fff" stroke-width="2" fill="none"/></svg>Full 3 stage 12 week training program</h4><p>The complete three stage home program with videos and printable plans to follow wherever suits you.</p></div>
    <div class="feature"><h4><svg width="18" height="18"><circle cx="9" cy="9" r="8" fill="#33a6d7"/><path d="M5 9l3 3 5-6" stroke="#fff" stroke-width="2" fill="none"/></svg>Full instructional manual DVD and program guide</h4><p>Clear guidance on every move so you can train safely and confidently from home.</p></div>
    <div class="feature"><h4><svg width="18" height="18"><circle cx="9" cy="9" r="8" fill="#33a6d7"/><path d="M5 9l3 3 5-6" stroke="#fff" stroke-width="2" fill="none"/></svg>Weekly accountability charts</h4><p>Record your progress every week and watch your results build over time.</p></div>
    <div class="feature"><h4><svg width="18" height="18"><circle cx="9" cy="9" r="8" fill="#33a6d7"/><path d="M5 9l3 3 5-6" stroke="#fff" stroke-width="2" fill="none"/></svg>Weekly coaching emails</h4><p>Encouragement and practical tips sent to you each week of the program.</p></div>
    <div class="feature"><h4><svg width="18" height="18"><circle cx="9" cy="9" r="8" fill="#33a6d7"/><path d="M5 9l3 3 5-6" stroke="#fff" stroke-width="2" fill="none"/></svg>Nutritional advice and healthy eating guidelines</h4><p>Easy eating habits that fit around feeding, naps and busy family days.</p></div>
    <div class="feature"><h4><svg width="18" height="18"><circle cx="9" cy="9" r="8" fill="#33a6d7"/><path d="M5 9l3 3 5-6" stroke="#fff" stroke-width="2" fill="none"/></svg>Healthy family friendly recipe book</h4><p>Simple, nourishing recipes the whole household will happily eat together.</p></div>
  </div>
  <p class="note" style="top:665px;font-size:11px">Please note: all you need to use this program is a mat, resistance band and a set of light hand weights.</p>
  <div class="product-shot" style="left:950px;top:635px;width:215px;height:190px" role="img" aria-label="Printed program materials"></div>
  <p class="price" style="top:780px">One time only payment of <b>$89</b><small>*including GST</small> That's only $7.42 per week!</p>
  <div class="center-btn" style="top:842px"><span class="btn">Get started now</span></div>
  <p class="postage" style="top:892px">Free postage</p>
</section>

<section class="why">
  <h2>Why our program is different</h2>
  <div class="card" style="left:130px;top:108px"><div class="photo" role="img" aria-label="Photo of a mother holding her baby"></div><h5>Specifically designed for mums</h5><p>Every workout is built around the needs of a recovering body, with gentle progressions that fit into naps and busy days at home.</p><span class="more">Read more</span></div>
  <div class="card" style="left:470px;top:108px"><div class="photo" style="background:linear-gradient(135deg,#b99bb8,#6e6a8c)" role="img" aria-label="Photo of a toddler playing with workout equipment"></div><h5>Workout equipment delivered so you can train from home</h5><p>No gym fees or childcare needed. Your kit arrives at your door so you can start straight away.</p><span class="more">Read more</span></div>
  <div class="card" style="left:130px;top:480px"><div class="photo" style="background:linear-gradient(135deg,#c9d68a,#7b8f4e)" role="img" aria-label="Photo of a green smoothie and fresh food"></div><h5>Delicious healthy family friendly recipes</h5><p>Meals that nourish you and the kids alike, quick to prepare and made from simple ingredients.</p><span class="more">Read more</span></div>
  <div class="card" style="left:470px;top:480px"><div class="photo" style="background:linear-gradient(135deg,#d7b9a4,#8f6f5c)" role="img" aria-label="Photo of a mother cuddling her child"></div><h5>Caters for mums at all stages of postnatal recovery</h5><p>Whether your baby is weeks or years old, the program adapts to where your body is right now.</p><span class="more">Read more</span></div>
  <div class="side social-box"><div class="top"></div><div class="title">Tidewell Mamas</div><div class="faces"><span></span><span></span><span></span><span></span><span></span><span></span></div></div>
  <div class="side side-cta"><p>Get more information about what the Tidewell Mamas program offers you</p><span class="btn">Read more</span></div>
  <div class="side side-join"><div class="photo" role="img" aria-label="Photo of a smiling mum in workout wear"></div><p>Take the first step today by joining our program</p><span class="btn">Get started now</span></div>
</section>

<section class="news">
  <h2>Top News</h2>
  <div class="news-arrows"><span></span><span></span></div>
  <div class="news-item" style="left:130px"><div class="thumb" role="img" aria-label="Blog photo"></div><div><h6>Easy ways to move more with a newborn</h6><time>22nd October 2016</time></div></div>
  <div class="news-item" style="left:455px"><div class="thumb" style="background:linear-gradient(135deg,#e2c47c,#9a7a32)" role="img" aria-label="Blog photo of a healthy meal"></div><div><h6>Quick lunch ideas for busy mums</h6><time>14th October 2016</time></div></div>
  <div class="news-item" style="left:780px"><div class="thumb" style="background:linear-gradient(135deg,#9fb0c0,#4d6070)" role="img" aria-label="Blog photo of a mum training"></div><div><h6>Staying motivated on tired days</h6><time>3rd October 2016</time></div></div>
</section>

<section class="compare">
  <h2>Compare our program to other Fitness and<br>weight loss strategies out there</h2>
  <h3>to see how much value for money you really get</h3>
  <table class="compare-table">
    <thead><tr><th></th><th>Tidewell Mamas Home Program</th><th>Other online programs</th><th>Group training</th><th>Personal training</th></tr></thead>
    <tbody>
      <tr><td>Flexible home program</td><td>✔</td><td>✔</td><td>✔</td><td>✔</td></tr>
      <tr><td>Instructional DVD</td><td>✔</td><td></td><td></td><td></td></tr>
      <tr><td>Healthy eating plan and recipe book</td><td>✔</td><td></td><td></td><td></td></tr>
      <tr><td>Exercise specially targeting mums</td><td>✔</td><td></td><td></td><td></td></tr>
      <tr><td>Over $100 worth of home gym equipment</td><td>✔</td><td></td><td></td><td></td></tr>
    </tbody>
    <tfoot><tr><td>Total cost</td><td>$199</td><td>$280</td><td>$480</td><td>$960</td></tr></tfoot>
  </table>
</section>

<footer class="site-footer">
  <div class="foot-brand">Tidewell Mamas</div>
  <p class="foot-text">Tidewell Mamas helps new mums feel strong, fit and confident again with home programs made for real life. www.tidewellmamas.com.au</p>
  <p class="foot-links">Home · About · Program · Store · Blog · Contact<br>Copyright © 2016 Tidewell Mamas. All rights reserved.</p>
  <div class="foot-social"><span></span><span></span></div>
</footer>

<div class="overlay"></div>
<div class="modal" role="dialog" aria-label="Free report offer">
  <div class="photo" role="img" aria-label="Photo of a fit mum in a lime green workout top"></div>
  <span class="close"></span>
  <div class="modal-logo"><span class="dot"></span><span class="name">Tidewell Mamas</span></div>
  <div class="modal-body">
    <h2>Get your FREE TOP 10 Baby Belly Blasting Tips</h2>
    <p>See our secret tips to a flatter yummy mummy tummy that you can start implementing <b>for free today!</b></p>
    <div class="modal-field">Name</div>
    <div class="modal-field">Email</div>
    <span class="btn">Get it free now!</span>
  </div>
</div>

</body>
</html>
```